Brightway Haus Inc. Business Card Design

Brightway Haus Inc. is in search of a great clean design for our business cards!

Looking to incorporate our full logo and watermark on side one (however, I am open to having the text and watermark separated within the design.)

On side two, I am looking to have contact information (Name, Position, Phone #, Email, Website (www.thebrightwayhaus.ca). Can have the logo and/or watermark as part of the design if applicable.

Please add tagline "Where Shine Counts" on either side 1 or 2. This tagline can be in a sans serif, serif or cursive font as long as it compliments overall design. Capitalization can be title or sentence case depending on how it fits within the design.

Get creative!! Looking for a clean, crisp, premium design! Looking for a glossy card finish with spot UV features when printed. Cards will also be printed with rounded corners. Standard dimensions (3.5 x 2).

Target Market(s)

B2B - primary clients are business owners or property management corporations. (residential jobs are few and far between)

Industry/Entity Type

Business

Contact Information for Business Card

- clean, crisp design
- double sided
- spot UV accents and glossy finish upon printing
- standard business card size (3.5 x 2) with rounded corners
- please see project description for requirements per side

Font styles to use
Sans Serif

Requirements
Must have
• - adequate bleeds with print ready files
• - cohesive design elements between side 1 & 2
• - spot UV elements (can be on both sides or just one, use your discretion)
• - colour pallet should match the logo file provided
• - incorporate tagline "where shine counts" (this tagline can be in a serif or sans serif font as long as it is complimentary to the overall design.
Nice to have
• - Premium elements with a clean design
Should not have
• - Please omit cartoon or whimsical like designs, think premium.
• - Colours should not stray from the pallet of the provided logo.

```html
<!DOCTYPE html>
<html lang="en">
<head>
<meta charset="utf-8">
<title>Brightway Haus Inc. Business Card</title>
<link href="https://fonts.googleapis.com/css2?family=Roboto:ital,wght@0,400;0,500;0,700;1,400&family=Roboto+Condensed:wght@400;700&display=swap" rel="stylesheet">
<style>
  :root {
    --page-bg: #3a3b3e;
    --card-bg: #242528;
    --card-edge: #2c2d31;
    --teal: #22c3c6;
    --navy: #2b3c8e;
    --white: #f2f3f5;
    --rule: #8a8d93;
  }
  * { box-sizing: border-box; margin: 0; padding: 0; }
  html, body {
    width: 1200px; height: 900px; overflow: hidden;
    background: var(--page-bg);
    font-family: "Roboto", Arial, sans-serif;
  }
  .sheet {
    width: 1200px; height: 900px;
    display: flex; flex-direction: column;
    align-items: center; justify-content: center; gap: 36px;
  }
  .card {
    position: relative;
    width: 700px; height: 400px;
    background: var(--card-bg);
    border: 1px solid var(--card-edge);
    border-radius: 14px;
    box-shadow: 0 10px 28px rgba(0,0,0,0.35);
  }

  /* Side one */
  .brand {
    position: absolute; left: 0; right: 0; top: 140px;
    display: flex; align-items: center; justify-content: center; gap: 14px;
  }
  .brand-dot {
    width: 34px; height: 34px; border-radius: 50%;
    background: var(--teal);
  }
  .brand-name {
    font-family: "Roboto", Arial, sans-serif;
    font-weight: 700; font-size: 44px; letter-spacing: 0.5px;
    color: var(--teal); text-transform: uppercase;
  }
  .tagline {
    position: absolute; left: 0; right: 0; top: 262px;
    display: flex; align-items: center; justify-content: center; gap: 10px;
  }
  .tagline-rule { width: 90px; height: 1px; background: var(--navy); }
  .tagline-text {
    font-style: italic; font-size: 19px; color: var(--navy);
  }
  .tagline-text strong { color: var(--teal); font-weight: 500; }

  /* Side two */
  .person {
    position: absolute; right: 400px; top: 118px; text-align: right;
  }
  .person-name {
    font-family: "Roboto Condensed", Arial, sans-serif;
    font-weight: 700; font-size: 40px; color: var(--teal);
    text-transform: uppercase; line-height: 1;
  }
  .person-role {
    font-family: "Roboto Condensed", Arial, sans-serif;
    font-size: 18px; color: var(--navy); text-transform: uppercase;
    margin-top: 6px;
  }
  .divider {
    position: absolute; left: 330px; top: 100px;
    width: 2px; height: 120px;
    background: linear-gradient(var(--card-bg), var(--rule), var(--card-bg));
  }
  .contacts {
    position: absolute; left: 360px; top: 104px;
    list-style: none;
  }
  .contacts li {
    display: flex; align-items: center; gap: 10px;
    font-size: 17px; font-weight: 500; color: var(--white);
    height: 24px;
  }
  .contacts svg, .address svg { width: 16px; height: 16px; flex: none; fill: var(--teal); }
  .address {
    position: absolute; left: 60px; bottom: 70px;
    display: flex; align-items: center; gap: 8px;
    font-size: 18px; font-weight: 500; color: var(--white);
  }
</style>
</head>
<body>
<main class="sheet">

  <section class="card card-front" aria-label="Card side one">
    <div class="brand">
      <span class="brand-dot"></span>
      <span class="brand-name">Brightway Haus Inc.</span>
    </div>
    <div class="tagline">
      <span class="tagline-rule"></span>
      <span class="tagline-text">Where <strong>Shine</strong> Counts</span>
      <span class="tagline-rule"></span>
    </div>
  </section>

  <section class="card card-back" aria-label="Card side two">
    <div class="person">
      <p class="person-name">Mara Ellison</p>
      <p class="person-role">CEO/Founder</p>
    </div>
    <span class="divider"></span>
    <ul class="contacts">
      <li>
        <svg viewBox="0 0 16 16" aria-hidden="true"><path d="M3.5 1l2.5 3-1.5 1.8c.9 2 2.6 3.7 4.7 4.7L11 9l3 2.5-1.5 2.5C7 14 2 9 2 3.5z"/></svg>
        902 555 0148
      </li>
      <li>
        <svg viewBox="0 0 16 16" aria-hidden="true"><path d="M4 1h8v14H4zM5.5 2.5v9.5h5V2.5zM7.2 13h1.6v1H7.2z" fill-rule="evenodd"/></svg>
        902 555 0193
      </li>
      <li>
        <svg viewBox="0 0 16 16" aria-hidden="true"><path d="M4 1h8v4H4zM1 6h14v6h-3v3H4v-3H1zM5.5 10v3.5h5V10z" fill-rule="evenodd"/></svg>
        902 555 0176
      </li>
      <li>
        <svg viewBox="0 0 16 16" aria-hidden="true"><path d="M1 3h14v10H1zM2 4l6 5 6-5v-.2H2z" fill-rule="evenodd"/></svg>
        mara@thebrightwayhaus.ca
      </li>
      <li>
        <svg viewBox="0 0 16 16" aria-hidden="true"><path d="M8 1a7 7 0 1 0 0 14A7 7 0 0 0 8 1zm-1 2.2C5 3.8 3.5 5.3 3.2 7H6zM9 3.2V7h3.8C12.5 5.3 11 3.8 9 3.2zM3.2 9C3.5 10.7 5 12.2 7 12.8V9zm5.8 0v3.8c2-.6 3.5-2.1 3.8-3.8z" fill-rule="evenodd"/></svg>
        www.thebrightwayhaus.ca
      </li>
    </ul>
    <p class="address">
      <svg viewBox="0 0 16 16" aria-hidden="true"><path d="M8 1a5 5 0 0 0-5 5c0 3.8 5 9 5 9s5-5.2 5-9a5 5 0 0 0-5-5zm0 3a2 2 0 1 1 0 4 2 2 0 0 1 0-4z" fill-rule="evenodd"/></svg>
      1420 Harbour Lane, Halifax, Nova Scotia B3H 2Y9
    </p>
  </section>

</main>
</body>
</html>
```